Business Cards for a law firm

Business cards for our law firm. Use our silhoette logo and OAK PARTNERS - check our website (www.oakpartners.example)

Contact Information for Business Card

our silhouette logo, OAK PARTNERS, 800-555-0147, Dorian Pemberton, dorian@oakpartners.example

Requirements
Must have
• our silhouette logo, OAK PARTNERS, 800-555-0147, Dorian Pemberton, dorian@oakpartners.example

```html
<!DOCTYPE html>
<html lang="en">
<head>
<meta charset="utf-8">
<title>Oak Partners – Business Cards</title>
<link rel="stylesheet" href="https://fonts.googleapis.com/css2?family=Roboto:wght@400;700&display=swap">
<style>
  :root {
    --navy: #243468;
    --white: #ffffff;
    --backdrop: #e3e7e9;
    --radius: 33px;
  }
  * { margin: 0; padding: 0; box-sizing: border-box; }
  html, body { width: 1200px; height: 960px; overflow: hidden; }
  body {
    background: var(--backdrop);
    font-family: "Roboto", Arial, sans-serif;
    position: relative;
  }
  .card {
    position: absolute;
    left: 250px;
    width: 701px;
    height: 401px;
    border-radius: var(--radius);
    overflow: hidden;
  }
  .card--front { top: 60px; background: var(--navy); color: var(--white); }
  .card--back { top: 500px; background: var(--white); color: var(--navy); }

  .brand {
    position: absolute;
    display: flex;
    align-items: center;
  }
  .brand__mark { background: currentColor; flex: none; }
  .brand__name {
    font-weight: 400;
    text-transform: uppercase;
    line-height: 0.92;
    letter-spacing: 0.02em;
  }
  .card--front .brand { left: 106px; top: 142px; gap: 22px; }
  .card--front .brand__mark { width: 64px; height: 64px; }
  .card--front .brand__name { font-size: 56px; }

  .card--back .brand { left: 24px; top: 36px; gap: 16px; }
  .card--back .brand__mark { width: 40px; height: 40px; }
  .card--back .brand__name { font-size: 38px; }

  .website {
    position: absolute;
    left: 0; right: 0;
    top: 410px;
    display: flex; align-items: center; justify-content: center;
    gap: 12px;
    font-size: 18.5px;
    letter-spacing: 0.03em;
  }
  .card--front .website { top: 411px; }
  .website, .card--front .website { top: auto; bottom: 27px; }

  .holder {
    position: absolute;
    left: 0; top: 283px;
    display: flex; align-items: center;
    height: 41px;
  }
  .holder__bar { width: 20px; height: 41px; background: var(--navy); }
  .holder__name {
    margin-left: 9px;
    font-size: 36px;
    letter-spacing: 0.02em;
    text-transform: uppercase;
    font-weight: 400;
  }
  .holder__name strong { font-weight: 700; }

  .rule {
    position: absolute;
    left: 30px; width: 651px;
    top: 338px;
    height: 2px;
    background: var(--navy);
  }
  .contact {
    position: absolute;
    top: 353px;
    display: flex; align-items: center; gap: 10px;
    font-size: 18.5px;
    letter-spacing: 0.03em;
  }
  .contact--phone { left: 30px; }
  .contact--email { right: 28px; }
  .icon { width: 18px; height: 18px; flex: none; }
</style>
</head>
<body>

  <section class="card card--front" aria-label="Card front">
    <div class="brand">
      <span class="brand__mark"></span>
      <span class="brand__name">Oak<br>Partners</span>
    </div>
    <p class="website">
      <svg class="icon" viewBox="0 0 20 20" aria-hidden="true">
        <circle cx="10" cy="10" r="8.5" fill="none" stroke="currentColor" stroke-width="1.8"/>
        <path d="M1.5 10h17M10 1.5c3 3 3 14 0 17M10 1.5c-3 3-3 14 0 17" fill="none" stroke="currentColor" stroke-width="1.4"/>
      </svg>
      www.oakpartners.example
    </p>
  </section>

  <section class="card card--back" aria-label="Card back">
    <div class="brand">
      <span class="brand__mark"></span>
      <span class="brand__name">Oak<br>Partners</span>
    </div>

    <div class="holder">
      <span class="holder__bar"></span>
      <h1 class="holder__name"><strong>Dorian</strong> Pemberton</h1>
    </div>

    <div class="rule"></div>

    <p class="contact contact--phone">
      <svg class="icon" viewBox="0 0 24 24" aria-hidden="true">
        <path fill="currentColor" d="M6.6 10.8a15.1 15.1 0 0 0 6.6 6.6l2.2-2.2a1 1 0 0 1 1-.25 11.4 11.4 0 0 0 3.6.57 1 1 0 0 1 1 1V20a1 1 0 0 1-1 1A17 17 0 0 1 3 4a1 1 0 0 1 1-1h3.5a1 1 0 0 1 1 1c0 1.25.2 2.45.57 3.57a1 1 0 0 1-.25 1z"/>
      </svg>
      800-555-0147
    </p>
    <p class="contact contact--email">
      <svg class="icon" viewBox="0 0 24 24" aria-hidden="true">
        <path fill="currentColor" d="M2 9l10-7 10 7v12H2z"/>
        <path fill="#ffffff" d="M4 10.5l8 5.5 8-5.5V19H4z" opacity=".25"/>
        <circle cx="12" cy="10" r="3" fill="none" stroke="#ffffff" stroke-width="1.5"/>
      </svg>
      dorian@oakpartners.example
    </p>
  </section>

</body>
</html>
```